Phuket Thailand - Rental Villa Website

I have a villa for rent in Thailand and require a website - i need to demo pictures/walk through video, local attractions, villa facilities description plus seaonal rates and online booking.

Industry/Entity Type

Rental

Coding

Coded - Design and coding required

```html
<!DOCTYPE html>
<html lang="en">
<head>
<meta charset="utf-8">
<title>Villa Rental – Phuket, Thailand</title>
<link rel="stylesheet" href="https://fonts.googleapis.com/css2?family=Open+Sans:wght@400;600;700&display=swap">
<style>
:root{
  --red:#c8321f;
  --yellow:#f2b619;
  --dark:#2d2424;
  --footer:#2a1f1f;
  --text:#555;
  --muted:#8aa3b8;
  --panel:#e6e0d8;
  --line:#d8d8d8;
  --white:#fff;
}
*{box-sizing:border-box;margin:0;padding:0}
html,body{width:725px;height:1200px;overflow:hidden}
body{position:relative;background:var(--white);font-family:"Open Sans",Arial,sans-serif;color:var(--text)}
.abs{position:absolute}
.logo{left:72px;top:14px;font-size:27px;font-weight:700;color:var(--red);letter-spacing:.5px}
.tagline{left:152px;top:46px;font-size:8px;color:#444}
.nav{left:318px;top:34px;display:flex;gap:21px;font-size:8px;text-transform:uppercase;color:#666}
.nav .active{color:var(--red)}
.btn-header{left:602px;top:24px;width:51px;height:20px;background:#3b3f4a;color:#fff;font-size:7px;display:flex;align-items:center;justify-content:center;border-radius:2px}
.hero-topline{left:0;top:72px;width:269px;height:4px;background:var(--dark)}
.hero-yellowbar{left:269px;top:72px;width:456px;height:11px;background:var(--yellow)}
.hero-photo{left:0;top:76px;width:725px;height:332px;background:linear-gradient(180deg,#5d6e58 0%,#7b8478 35%,#b9b0a2 65%,#d2c7b6 100%)}
.hero-bottomline{left:269px;top:408px;width:456px;height:5px;background:var(--dark)}
.hero-arrow{top:234px;width:19px;height:18px;background:rgba(45,36,36,.8);display:flex;align-items:center;justify-content:center}
.hero-caption{left:0;top:346px;width:269px;height:67px;background:var(--yellow)}
.hero-title{left:73px;top:355px;font-size:16px;font-weight:700;color:var(--dark)}
.btn-outline-dark{left:74px;top:380px;width:64px;height:20px;border:1px solid var(--dark);font-size:7.5px;font-weight:700;color:var(--dark);display:flex;align-items:center;justify-content:center}
.welcome-title{left:72px;top:424px;font-size:24px;font-weight:700;color:var(--muted)}
.welcome-text{left:72px;top:460px;width:182px;font-size:8px;line-height:13.6px}
.video{left:72px;top:538px;width:178px;height:91px;background:linear-gradient(135deg,#4a3a33,#2a2422 60%,#7a7268)}
.video-play{left:147px;top:569px;width:28px;height:28px;border-radius:50%;border:2px solid #fff;background:rgba(0,0,0,.35);display:flex;align-items:center;justify-content:center}
.booking{left:269px;top:413px;width:384px;height:216px;background:var(--panel)}
.booking-title{left:294px;top:425px;font-size:16px;font-weight:700;color:var(--dark)}
.field{background:#fff;font-size:8px;color:#666;padding:0 10px;display:flex;align-items:center;justify-content:space-between}
.field.area{align-items:flex-start;padding-top:9px}
.btn-dark{background:var(--dark);color:#fff;font-size:8px;display:flex;align-items:center;justify-content:center}
.divider{left:72px;top:657px;width:580px;height:1px;background:var(--line)}
.section-title{font-size:16px;font-weight:700;color:#444}
.facilities-photo{left:73px;top:709px;width:178px;height:96px;background:linear-gradient(135deg,#5b6a43 0%,#4b4d4a 45%,#7d5a4b 100%)}
.facilities-text{left:72px;top:813px;width:182px;font-size:8px;line-height:13px}
.facility{left:72px;display:flex;align-items:center;gap:12px;font-size:11.5px;color:var(--red)}
.facility svg{width:14px;height:14px}
.btn-outline-red{left:74px;top:1026px;width:64px;height:21px;border:1px solid var(--red);color:var(--red);font-size:7.5px;display:flex;align-items:center;justify-content:center}
.card{top:709px;width:122px;height:150px;border:1px solid var(--line)}
.card-photo{height:96px}
.card-title{position:absolute;left:10px;top:104px;font-size:9.5px;color:#444}
.card-link{position:absolute;left:10px;top:124px;font-size:7.5px;color:#555;text-decoration:underline;display:flex;gap:3px;align-items:center}
.rates{left:270px;top:875px;width:382px;height:80px;background:linear-gradient(180deg,#8fb1cc 0%,#5f7f52 40%,#3f5735 100%)}
.rates-label{left:270px;top:930px;width:135px;height:25px;background:var(--yellow);color:#fff;font-size:13px;font-weight:700;display:flex;align-items:center;justify-content:center}
.rates-btn{left:405px;top:930px;width:79px;height:25px;background:var(--dark);color:#fff;font-size:11px;font-weight:600;display:flex;align-items:center;justify-content:center}
.newsletter{left:269px;top:973px;width:383px;height:74px;border:1px solid #a9bfd0}
.newsletter-title{left:293px;top:984px;font-size:11px;font-weight:600;color:#444}
.nl-field{top:1005px;height:24px;border:1px solid #ccc;font-size:8px;color:#666;padding-left:10px;display:flex;align-items:center}
.btn-yellow{left:573px;top:1005px;width:55px;height:24px;background:var(--yellow);color:#333;font-size:8px;display:flex;align-items:center;justify-content:center}
.footer{left:0;top:1088px;width:725px;height:112px;background:var(--footer)}
.footer-links{left:0;top:1105px;width:725px;text-align:center;font-size:8px;color:#ccc}
.footer-links .sep{color:#777;margin:0 5px}
.copyright{left:0;top:1125px;width:725px;text-align:center;font-size:8px;color:#ccc}
.social{top:1152px;width:28px;height:28px;border-radius:50%;background:#fff}
</style>
</head>
<body>
<header>
  <div class="abs logo">Villa Rental</div>
  <div class="abs tagline">Service in Phuket, Thailand</div>
  <nav class="abs nav"><span class="active">Home</span><span>Villa Facilities</span><span>Places</span><span>Rates</span><span>Contact Us</span></nav>
  <div class="abs btn-header">BOOK NOW</div>
</header>

<section class="hero">
  <div class="abs hero-photo" role="img" aria-label="Villa terrace with wooden roof beams overlooking a lake and green hills"></div>
  <div class="abs hero-topline"></div>
  <div class="abs hero-yellowbar"></div>
  <div class="abs hero-bottomline"></div>
  <div class="abs hero-arrow" style="left:0"><svg width="9" height="9" viewBox="0 0 10 10"><path d="M9 5H2M5 1.5 1.5 5 5 8.5" stroke="#fff" stroke-width="2" fill="none"/></svg></div>
  <div class="abs hero-arrow" style="left:706px;background:none"><svg width="9" height="9" viewBox="0 0 10 10"><path d="M1 5h7M5 1.5 8.5 5 5 8.5" stroke="#fff" stroke-width="2" fill="none"/></svg></div>
  <div class="abs hero-caption"></div>
  <h1 class="abs hero-title">PROIN EGET CONGUE</h1>
  <div class="abs btn-outline-dark">BOOK NOW</div>
</section>

<section class="welcome">
  <h2 class="abs welcome-title">WELCOME!</h2>
  <p class="abs welcome-text">Pellentesque convallis molestie enim sit amet efficitur. Etiam id imperdiet lectus. Vivamus lacus justo, ultrices nec erat in, euismod iaculis mauris. Vivamus eleifend vitae nulla vel male suada. In ac malesuada lacus.</p>
  <div class="abs video" role="img" aria-label="Walk-through video of the villa bedroom"></div>
  <div class="abs video-play" aria-label="Play video"><svg width="9" height="10" viewBox="0 0 9 10"><path d="M1.5 0.5l7 4.5-7 4.5z" fill="#fff"/></svg></div>
</section>

<section class="booking-form">
  <div class="abs booking"></div>
  <h2 class="abs booking-title">BOOK NOW</h2>
  <div class="abs field" style="left:296px;top:456px;width:160px;height:26px">Name</div>
  <div class="abs field" style="left:468px;top:456px;width:161px;height:26px">E-mail</div>
  <div class="abs field" style="left:296px;top:493px;width:74px;height:26px">Adults : 2 <svg width="8" height="5"><path d="M0 0h8L4 5z" fill="#aaa"/></svg></div>
  <div class="abs field" style="left:383px;top:493px;width:74px;height:26px">Kids : 2 <svg width="8" height="5"><path d="M0 0h8L4 5z" fill="#aaa"/></svg></div>
  <div class="abs field" style="left:474px;top:493px;width:69px;height:26px">From <svg width="16" height="14" viewBox="0 0 16 14"><rect x=".5" y="1.5" width="15" height="12" fill="none" stroke="#bbb"/><path d="M.5 5h15M4 5v9M8 5v9M12 5v9M.5 9h15" stroke="#bbb"/></svg></div>
  <div class="abs field" style="left:554px;top:493px;width:74px;height:26px">To <svg width="16" height="14" viewBox="0 0 16 14"><rect x=".5" y="1.5" width="15" height="12" fill="none" stroke="#bbb"/><path d="M.5 5h15M4 5v9M8 5v9M12 5v9M.5 9h15" stroke="#bbb"/></svg></div>
  <div class="abs field area" style="left:296px;top:530px;width:331px;height:51px">Message</div>
  <div class="abs btn-dark" style="left:566px;top:590px;width:62px;height:24px">BOOK NOW</div>
</section>

<div class="abs divider"></div>

<section class="facilities">
  <h2 class="abs section-title" style="left:73px;top:682px">VILLA FACILITIES</h2>
  <div class="abs facilities-photo" role="img" aria-label="Villa exterior with tiled roof and garden"></div>
  <p class="abs facilities-text">Nunc sit amet consequat risus. Curabitur ac elit leo. In eleifend dui tellus, in scelerisque elit porttitor et. Integer eu massa lacinia.</p>
  <div class="abs facility" style="top:865px"><svg viewBox="0 0 14 14"><path d="M2 0v5q0 2 2 2v7M4 0v5M6 0v5q0 2-2 2M10 14V0q3 2 3 7h-3" stroke="var(--red)" stroke-width="1.4" fill="none"/></svg>Restaurant</div>
  <div class="abs facility" style="top:896px"><svg viewBox="0 0 14 14"><path d="M3 1h4l-.5 4a1.5 1.5 0 0 1-3 0zM5 6v7M3 13h4M9 2l3 1-1 3.5M10.5 6l-1 7" stroke="var(--red)" stroke-width="1.2" fill="none"/></svg>Wines</div>
  <div class="abs facility" style="top:927px"><svg viewBox="0 0 14 14"><path d="M0 6h9a2 2 0 1 0-2-2M0 9h12a1.5 1.5 0 1 1-1.5 1.5" stroke="var(--red)" stroke-width="1.4" fill="none"/></svg>Natural Air</div>
  <div class="abs facility" style="top:958px"><svg viewBox="0 0 14 14"><path d="M2 12q0-8 5-8t5 8zM0 12.5h14M7 2v2" stroke="var(--red)" stroke-width="1.4" fill="var(--red)"/></svg>Best Room Service</div>
  <div class="abs facility" style="top:989px"><svg viewBox="0 0 14 14"><path d="M1 5a9 9 0 0 1 12 0M3 7.5a6 6 0 0 1 8 0M5 10a3 3 0 0 1 4 0" stroke="var(--red)" stroke-width="1.6" fill="none"/><circle cx="7" cy="12" r="1.2" fill="var(--red)"/></svg>Wi-fi</div>
  <div class="abs btn-outline-red">READ MORE</div>
</section>

<section class="attractions">
  <h2 class="abs section-title" style="left:270px;top:682px">LOCAL ATTRACTIONS</h2>
  <svg class="abs" style="left:640px;top:686px" width="12" height="12" viewBox="0 0 12 12"><circle cx="6" cy="6" r="5.3" fill="none" stroke="#888"/><path d="M3 6h5M6 3.8 8.2 6 6 8.2" stroke="#888" fill="none"/></svg>
  <div class="abs card" style="left:270px"><div class="card-photo" role="img" aria-label="Turquoise beach with swimmers" style="background:linear-gradient(180deg,#2f7fd0,#4fc6d8 55%,#e8e2cf)"></div><div class="card-title">Aliquam erat volutpat</div><div class="card-link"><svg width="6" height="8" viewBox="0 0 6 8"><path d="M3 8 .6 4A2.6 2.6 0 1 1 5.4 4z" fill="#555"/></svg>Find on Map</div></div>
  <div class="abs card" style="left:400px"><div class="card-photo" role="img" aria-label="Ancient temple ruins reflected in a lotus pond" style="background:linear-gradient(180deg,#8bb7d9,#7c7a52 45%,#3d4a2e)"></div><div class="card-title">Aliquam erat volutpat</div><div class="card-link"><svg width="6" height="8" viewBox="0 0 6 8"><path d="M3 8 .6 4A2.6 2.6 0 1 1 5.4 4z" fill="#555"/></svg>Find on Map</div></div>
  <div class="abs card" style="left:530px"><div class="card-photo" role="img" aria-label="Old town clock tower building at dusk" style="background:linear-gradient(180deg,#2b4fa0,#6a5a8a 40%,#c46a2a)"></div><div class="card-title">Aliquam erat volutpat</div><div class="card-link"><svg width="6" height="8" viewBox="0 0 6 8"><path d="M3 8 .6 4A2.6 2.6 0 1 1 5.4 4z" fill="#555"/></svg>Find on Map</div></div>
  <div class="abs rates" role="img" aria-label="Limestone cliffs above the sea"></div>
  <div class="abs rates-label">SEASONAL RATES</div>
  <div class="abs rates-btn">BOOK NOW</div>
  <div class="abs newsletter"></div>
  <h3 class="abs newsletter-title">NEWSLETTER SUBSCRIBE</h3>
  <div class="abs nl-field" style="left:294px;width:136px">Name</div>
  <div class="abs nl-field" style="left:434px;width:136px">E-mail</div>
  <div class="abs btn-yellow">Subscribe</div>
</section>

<footer>
  <div class="abs footer"></div>
  <div class="abs footer-links">Home<span class="sep">/</span>Villa Facilities<span class="sep">/</span>Places<span class="sep">/</span>Rates<span class="sep">/</span>Contact us</div>
  <div class="abs copyright">Copyright © 2015 Villa Rental. All rights reserved.</div>
  <div class="abs social" style="left:280px" aria-label="Social link"></div>
  <div class="abs social" style="left:307px" aria-label="Social link"></div>
  <div class="abs social" style="left:334px" aria-label="Social link"></div>
  <div class="abs social" style="left:361px" aria-label="Social link"></div>
  <div class="abs social" style="left:388px" aria-label="Social link"></div>
  <div class="abs social" style="left:415px" aria-label="Social link"></div>
</footer>
</body>
</html>
```